A private security company called "Tavron Security Services Ltd"

Hello everybody,

We need a web page for a company based in NZ. It is mainly an informative website so it would be wonderful if the designer puts their absolute best into making it a website that I would really appreciate. The website needs to show professionalism and also needs to make our web surfers find the information they need in a click. the company's colour is black and silver, and if those two colours could be integrated into the website it would be absolutely lovely. Please do contact me for any information.

Sincerely,
Dorian Vaskel

Industry/Entity Type

Security

```html
<!DOCTYPE html>
<html lang="en">
<head>
<meta charset="utf-8">
<title>Tavron Security Services Ltd</title>
<link href="https://fonts.googleapis.com/css2?family=Open+Sans:wght@300;400;600;700&family=Raleway:wght@300;700&display=swap" rel="stylesheet">
<style>
  :root {
    --ink: #1f1f1f;
    --ink-deep: #141414;
    --gold: #fcc50a;
    --paper: #ffffff;
    --text-soft: #9a9a9a;
    --text-mid: #555555;
    --rule: #e2e2e2;
    --footer-text: #8c8c8c;
  }
  * { margin: 0; padding: 0; box-sizing: border-box; }
  html, body { width: 996px; height: 1200px; overflow: hidden; background: var(--paper); }
  body { position: relative; font-family: "Open Sans", sans-serif; color: var(--ink); }
  .backdrop { position: absolute; left: 0; top: 0; }
  .abs { position: absolute; }

  .brand { left: 92px; top: 40px; color: var(--paper); font-family: "Open Sans", sans-serif; font-weight: 600; font-size: 14px; line-height: 17px; letter-spacing: 1px; text-align: center; width: 104px; }
  .brand-mark { left: 133px; top: 14px; width: 22px; height: 22px; border-radius: 50%; background: var(--paper); }

  .nav { left: 437px; top: 0; display: flex; height: 80px; align-items: center; list-style: none; }
  .nav li { font-size: 12.5px; color: var(--paper); margin-right: 27px; white-space: nowrap; }
  .nav li.current { color: var(--ink); width: 87px; text-align: center; margin-right: 22px; font-weight: 400; }

  .hero-title { left: 0; width: 996px; top: 138px; text-align: center; font-family: "Raleway", sans-serif; font-weight: 300; font-size: 42px; color: #111; letter-spacing: -0.5px; }
  .hero-title b { font-weight: 700; }

  .feature { top: 210px; width: 196px; height: 312px; }
  .feature-photo { width: 100%; height: 270px; }
  .feature-caption { height: 42px; background: #2a2a2a; color: var(--paper); font-size: 15px; text-align: center; line-height: 42px; }

  h2.section { font-weight: 400; font-size: 21px; color: var(--ink); }
  h2.who-title { left: 90px; top: 558px; font-size: 24px; font-weight: 600; }
  .team-photo { left: 90px; top: 615px; width: 194px; height: 132px; background: linear-gradient(135deg, #d9dadc, #8a8c90 55%, #3a3b3f); }
  .copy { font-size: 11px; line-height: 16.6px; color: var(--text-soft); font-weight: 300; }
  .copy a { color: var(--ink); font-weight: 400; text-decoration: underline; }
  .btn { display: block; width: 75px; height: 27px; background: #111; color: var(--paper); font-size: 10.5px; line-height: 27px; text-align: center; clip-path: polygon(0 0, 100% 0, 98% 100%, 0 100%); }

  .col-rule { width: 1px; background: var(--rule); top: 565px; height: 355px; }
  .news-item { border-bottom: 1px solid var(--rule); padding: 0 0 11px 4px; margin-bottom: 11px; width: 178px; }
  .news-date { font-size: 10.5px; color: var(--ink); text-decoration: underline; margin-bottom: 5px; }
  .section-icon { width: 34px; height: 34px; border-radius: 4px; background: linear-gradient(135deg, #d8d8d8, #6d6d6d); }

  .service-list { list-style: none; width: 168px; }
  .service-list li { font-size: 10.5px; color: var(--text-mid); height: 25px; line-height: 23px; border-bottom: 1px solid var(--rule); padding-left: 14px; position: relative; }
  .service-list li::before { content: ""; position: absolute; left: 3px; top: 9px; border-left: 4px solid #999; border-top: 3px solid transparent; border-bottom: 3px solid transparent; }
  .service-list li.active::before { border-left-color: var(--gold); }

  .footer-title { font-size: 17px; font-weight: 600; color: var(--paper); }
  .footer-list { list-style: none; margin-top: 11px; }
  .footer-list li { font-size: 10px; color: var(--footer-text); line-height: 18.3px; padding-left: 9px; position: relative; }
  .footer-list li::before { content: ""; position: absolute; left: 0; top: 7px; border-left: 3px solid #bbb; border-top: 2px solid transparent; border-bottom: 2px solid transparent; }
  .footer-list li.current { color: var(--paper); }
  .contact-copy { font-size: 10.5px; color: var(--footer-text); line-height: 16.6px; }
  .social { display: flex; gap: 4px; }
  .social span { width: 13px; height: 13px; background: #777; border-radius: 2px; }

  .legal { left: 0; top: 1167px; width: 996px; height: 33px; background: var(--ink-deep); color: #d0d0d0; font-size: 10.5px; }
  .legal span { position: absolute; top: 10px; }
</style>
</head>
<body>

<svg class="backdrop" width="996" height="1200" viewBox="0 0 996 1200" aria-hidden="true">
  <rect x="0" y="0" width="996" height="444" fill="var(--gold)"/>
  <polygon points="0,0 437,0 437,83 0,98" fill="var(--ink)"/>
  <polygon points="524,0 996,0 996,62 524,80" fill="var(--ink)"/>
  <polygon points="0,979 996,944 996,1200 0,1200" fill="var(--ink)"/>
</svg>

<div class="abs brand-mark"></div>
<div class="abs brand">TAVRON<br><span style="font-size:8px;letter-spacing:0">Security Services Ltd.</span></div>

<ul class="abs nav">
  <li class="current">HOME</li>
  <li>About Us</li>
  <li>Security Services</li>
  <li>Testimonials</li>
  <li>Contct Us</li>
</ul>

<h1 class="abs hero-title">We <b>Guarantee</b> Your <b>Safety</b></h1>

<div class="abs feature" style="left:90px">
  <div class="feature-photo" role="img" aria-label="Fixed outdoor security camera against trees" style="background:linear-gradient(160deg,#3f6b45,#c9d3cf 60%,#8f9a9a)"></div>
  <div class="feature-caption">Fixed Camra Systems</div>
</div>
<div class="abs feature" style="left:295px">
  <div class="feature-photo" role="img" aria-label="Security cameras mounted against blue sky" style="background:linear-gradient(160deg,#3b6fa8,#cfe0ee 55%,#bfc3c6)"></div>
  <div class="feature-caption">Camera Systems</div>
</div>
<div class="abs feature" style="left:500px">
  <div class="feature-photo" role="img" aria-label="Dome security camera close-up" style="background:linear-gradient(160deg,#c9cacc,#e8e9ea 50%,#d2d3d5)"></div>
  <div class="feature-caption">Fixed Camra Systems</div>
</div>
<div class="abs feature" style="left:705px;width:200px">
  <div class="feature-photo" role="img" aria-label="Alarm keypad with fingerprint reader on wall" style="background:linear-gradient(135deg,#f4f4f4,#d5d6d8 60%,#b8b9bc)"></div>
  <div class="feature-caption">Alarm System</div>
</div>

<h2 class="abs section who-title">WHO WE ARE ?</h2>
<div class="abs team-photo" role="img" aria-label="Team of four staff in business suits"></div>
<p class="abs copy" style="left:297px;top:612px;width:190px">Lorem ipsum dolor sit&nbsp; consectetur adipisicing elit eiusmod&nbsp; incididunt ut labore et dolore magna aliqua ut enim ad minim veniam.</p>
<p class="abs copy" style="left:297px;top:695px;width:190px">quis nostrud exercitation ullamco laboris nisi ut aliquip ex commodo</p>
<p class="abs copy" style="left:89px;top:756px;width:390px"><a>Lorem ipsum dolor sit amet, consectetur adipisicing elit</a> sed do eiusmod tempor incididunt ut labore et dolore magna aliqua ut enim ad minim.</p>
<p class="abs copy" style="left:89px;top:806px;width:390px">veniam, quis nostrud exercitation ullamco laboris nisi ut aliquip ex ea commodo consequat duis aute irure dolor reprehenderit in voluptate velit esse cillum dolore eu fugiat nulla pariatur excepteur sint occaecat cupidatat</p>
<a class="abs btn" style="left:89px;top:882px">Read More</a>

<div class="abs col-rule" style="left:511px"></div>

<h2 class="abs section" style="left:529px;top:566px">Latest News</h2>
<div class="abs section-icon" role="img" aria-label="News tablet illustration" style="left:672px;top:563px"></div>
<div class="abs" style="left:526px;top:615px">
  <div class="news-item"><p class="news-date">6.24.2014</p><p class="copy">Dolore magna aliqua ut enim ad laboris nisi ut aliquip commodo consequat duis aute irure dolor.</p></div>
  <div class="news-item"><p class="news-date">6.24.2014</p><p class="copy">Dolore magna aliqua ut enim ad laboris nisi ut aliquip commodo consequat duis aute irure dolor.</p></div>
  <div class="news-item" style="border-bottom:none"><p class="news-date">6.24.2014</p><p class="copy">Dolore magna aliqua ut enim ad laboris nisi ut aliquip commodo consequat duis aute irure dolor.</p></div>
</div>
<a class="abs btn" style="left:530px;top:882px">Read More</a>

<div class="abs col-rule" style="left:720px"></div>

<h2 class="abs section" style="left:737px;top:566px">Services</h2>
<div class="abs section-icon" role="img" aria-label="Computer illustration" style="left:877px;top:562px"></div>
<ul class="abs service-list" style="left:732px;top:609px">
  <li class="active">Lorem ipsum dolor sit amet</li>
  <li>Consectetur adipisicing elit</li>
  <li>Sed do eiusmod tempor</li>
  <li>Incididunt ut labore et dolore</li>
  <li>Magna aliqua ut enim ad</li>
  <li>Minim veniam, quis nostrud</li>
  <li>Exercitation ullamco laboris</li>
  <li>Nisi ut aliquip commodo</li>
  <li>Consequat duis aute irure</li>
  <li>Dolor in reprehenderit in</li>
</ul>
<a class="abs btn" style="left:738px;top:882px">Read More</a>

<div class="abs" style="left:122px;top:999px">
  <h3 class="footer-title">Site Map</h3>
  <ul class="footer-list">
    <li class="current">Home</li><li>About Us</li><li>Security Services</li><li>Testimonials</li><li>Contct Us</li>
  </ul>
</div>
<div class="abs" style="left:288px;top:999px">
  <h3 class="footer-title">Related links</h3>
  <ul class="footer-list">
    <li>Lorem ipsum dolor</li><li>sit amet Consectetur</li><li>adipisicing elit Sed</li><li>do eiusmod tempor</li><li>Incididunt ut labore</li>
  </ul>
</div>
<div class="abs" style="left:454px;top:999px">
  <h3 class="footer-title">For Clients</h3>
  <ul class="footer-list">
    <li>Sign Up</li><li>Forum</li><li>Policy</li>
  </ul>
</div>
<svg class="abs" style="left:684px;top:1003px" width="20" height="15" viewBox="0 0 20 15" aria-hidden="true">
  <polygon points="0,5 10,0 20,5 20,15 0,15" fill="#bdbdbd"/>
  <polyline points="0,5 10,11 20,5" fill="none" stroke="#555" stroke-width="1.2"/>
</svg>
<div class="abs" style="left:714px;top:999px">
  <h3 class="footer-title">Contact Information</h3>
  <p class="contact-copy" style="margin-top:11px;width:170px">Dolore magna aliqua ut enim ad laboris nisi ut aliquip</p>
  <p class="contact-copy" style="margin-top:5px">E-mail: info@tavronsecurity.co.nz</p>
  <p class="contact-copy" style="margin-top:6px">Phone: +64 9 555 0142</p>
  <div class="social" style="margin-top:12px"><span></span><span></span><span></span></div>
</div>

<div class="abs legal">
  <span style="left:89px">Copy rigthe 2014 © Tavron. All rights reserved</span>
  <span style="right:91px">Privacy Policy</span>
</div>

</body>
</html>
```